Garlic Farm for Farm Sales/Restaurant sales

Need a professional, but appealing to agriculture world. We are selling 27 kinds of Organic Garlic from a farm in Simla,CO. I have uploaded logo and business information-we are going to need a template, because I will need to use it for four separate people.
-We are trying to appeal to Farm to table restaurants
-As well as growers/farmers

Target Market(s)

Agriculture Sales/Restaurants-Organic

Industry/Entity Type

Agriculture

Contact Information for Business Card

Want it to look more unique then your average kelto stock card- I want it to look amazing

Font styles to use
Sans Serif

Colors
0455a3
ec1f27
fbed22
ffffff

Requirements
Must have
• Just be creative
Nice to have
• Colorful
Should not have
• plain

```html
<!DOCTYPE html>
<html lang="en">
<head>
<meta charset="utf-8">
<title>Prairie Clove Garlic – Business Card</title>
<link rel="stylesheet" href="https://fonts.googleapis.com/css2?family=Source+Sans+3:wght@400;600&display=swap">
<style>
  :root {
    --brand-blue: #0455a3;
    --brand-red: #ec1f27;
    --band-red: #c91f3a;
    --brand-yellow: #fbed22;
    --card-white: #ffffff;
    --ink: #1d1d1f;
    --backdrop: #e9e4dc;
  }
  * { margin: 0; padding: 0; box-sizing: border-box; }
  html, body {
    width: 1200px; height: 892px; overflow: hidden;
    background: var(--backdrop);
    font-family: "Source Sans 3", Arial, sans-serif;
  }
  .canvas {
    position: relative; width: 1200px; height: 892px;
  }
  .card {
    position: absolute; top: 291px;
    width: 540px; height: 309px;
    background: var(--card-white);
    box-shadow: 0 8px 24px rgba(0,0,0,.18);
    overflow: hidden;
  }
  /* Back of card */
  .card-back { left: 40px; }
  .back-brand {
    position: absolute; inset: 0;
    display: flex; flex-direction: column; align-items: center; justify-content: center; gap: 18px;
  }
  .brand-dot {
    width: 72px; height: 72px; border-radius: 50%;
    background: var(--brand-red);
  }
  .back-name {
    font-size: 40px; font-weight: 600; color: var(--brand-blue);
    letter-spacing: .5px;
  }
  /* Front of card */
  .card-front { left: 620px; }
  .front-brand {
    position: absolute; left: 30px; top: 58px; width: 200px;
    display: flex; flex-direction: column; align-items: flex-start; gap: 14px;
  }
  .front-brand .brand-dot { width: 44px; height: 44px; }
  .front-name {
    font-size: 28px; line-height: 1.05; font-weight: 400; color: var(--brand-blue);
    text-transform: uppercase; letter-spacing: 1.5px;
  }
  .divider {
    position: absolute; left: 250px; top: 20px; width: 1px; height: 220px;
    background: var(--brand-blue); opacity: .7;
  }
  .contact {
    position: absolute; left: 272px; top: 30px; right: 24px;
  }
  .person-name {
    font-size: 30px; font-weight: 400; color: var(--brand-red);
    text-align: right; margin-bottom: 22px;
  }
  .phone-list { list-style: none; }
  .phone-list li {
    display: flex; align-items: center; gap: 10px;
    font-size: 16px; color: var(--ink); line-height: 22px;
  }
  .phone-list svg { width: 16px; height: 16px; flex: none; }
  .address {
    margin-top: 14px; font-size: 15px; color: var(--ink);
  }
  .web-band {
    position: absolute; left: 0; right: 0; bottom: 0; height: 58px;
    background: var(--band-red);
    display: flex; align-items: center; justify-content: center; gap: 12px;
    color: var(--card-white); font-size: 14px;
  }
</style>
</head>
<body>
<main class="canvas">
  <section class="card card-back" aria-label="Card back">
    <div class="back-brand">
      <span class="brand-dot"></span>
      <span class="back-name">Prairie Clove Garlic</span>
    </div>
  </section>

  <section class="card card-front" aria-label="Card front">
    <div class="front-brand">
      <span class="brand-dot"></span>
      <span class="front-name">Prairie Clove Garlic</span>
    </div>
    <div class="divider"></div>
    <div class="contact">
      <p class="person-name">Dana Whitfield</p>
      <ul class="phone-list">
        <li>
          <svg viewBox="0 0 16 16" aria-hidden="true"><rect width="16" height="16" rx="2" fill="var(--brand-blue)"/><path d="M5 4c1 0 1.5 2 1 2.5s0 2 2.5 3.5 2.5.5 3 .5 1 1.5 0 2-4 0-6-2.5S4 4 5 4z" fill="#fff"/></svg>
          555-014-2286
        </li>
        <li>
          <svg viewBox="0 0 16 16" aria-hidden="true"><rect width="16" height="16" rx="2" fill="var(--brand-blue)"/><rect x="5" y="3" width="6" height="10" rx="1" fill="#fff"/></svg>
          555-014-2286
        </li>
        <li>
          <svg viewBox="0 0 16 16" aria-hidden="true"><rect width="16" height="16" rx="2" fill="var(--brand-blue)"/><rect x="3" y="6" width="10" height="6" fill="#fff"/><rect x="5" y="3" width="6" height="3" fill="#fff"/></svg>
          555-014-2286
        </li>
      </ul>
      <p class="address">88 Harvest Road Limon, CO 80828</p>
    </div>
    <div class="web-band">
      <span>dwhitfield@prairieclove.com</span>
      <span>|</span>
      <span>www.prairieclove.com</span>
    </div>
  </section>
</main>
</body>
</html>
```